Updated look for company collateral

We are a staffing company specializing in placing accounting, finance and IT professionals in their next career. We are going through a rebrand as well, i have included several other pieces so you can see our vision for the future. We are looking for a front and back one pager. We have four divisions Our company needs an updated look for our company collateral - there are four versions of the content (Enterprise, IT, Healthcare IT and Accounting & Finance) the design will be the same (different images for each flyer but same template) I am looking for a template that could be updated for each division. I am including the content for the IT version.

Our design aesthetic is clean, well organized, but with interesting design elements. We want to be perceived as on trend, leader in our industry. We have been in business for almost 20 years and know our industry well and successfully, our workforce is youthful, energetic and competitive so we still want to have an element of fun and creativity in our collateral.

Font styles to use
Sans Serif

Requirements
Must have
• similar color themes as attached examples

```html
<!DOCTYPE html>
<html lang="en">
<head>
<meta charset="utf-8">
<title>Veltro Group – Division Overview IT</title>
<link href="https://fonts.googleapis.com/css2?family=Raleway:wght@400;500;600;700;800&family=Montserrat:wght@300;800;900&family=Oswald:wght@500;600&display=swap" rel="stylesheet">
<style>
:root{
  --navy:#2c3a4c;
  --orange:#f07f2d;
  --orange-dark:#c9601a;
  --panel:#efefef;
  --row:#e7e7e7;
  --white:#ffffff;
  --ink:#3b3b3b;
  --stage:#9b9b9b;
}
*{margin:0;padding:0;box-sizing:border-box}
html,body{width:1200px;height:848px;overflow:hidden;background:var(--stage)}
body{position:relative;font-family:'Raleway',sans-serif;color:var(--ink)}
.page{position:absolute;top:61px;width:514px;height:726px;background:var(--panel);overflow:hidden;box-shadow:0 4px 14px rgba(0,0,0,.25)}
.page.front{left:57px}
.page.back{left:626px}
.abs{position:absolute}
.body-text{font-size:7.6px;line-height:9.9px;text-align:justify}
.body-text p+p{margin-top:4px}
.hl{color:var(--orange)}

/* front header */
.hero{left:0;top:0;width:514px;height:246px;background:var(--navy);border-bottom-left-radius:44px;overflow:hidden}
.hero-photo{position:absolute;left:230px;top:0;width:284px;height:246px;background:linear-gradient(90deg,var(--navy) 0%,#5c6b7b 22%,#9aa6ae 55%,#c9cfd2 100%)}
.brand{display:flex;flex-direction:column;align-items:center;left:20px;width:205px;top:25px}
.brand-mark{width:44px;height:44px;border-radius:50%;background:var(--orange)}
.brand-name{margin-top:12px;font-family:'Raleway',sans-serif;font-weight:600;font-size:21px;letter-spacing:3.2px;color:var(--white);white-space:nowrap}
.headline{left:23px;top:120px;font-family:'Montserrat',sans-serif;font-weight:900;font-size:31px;line-height:29px;color:var(--white);letter-spacing:-.5px}
.headline .light{font-weight:300}
.tagline{left:25px;top:214px;font-size:9.6px;color:var(--white);font-weight:500}
.division-tab{left:333px;top:215px;width:181px;height:31px;background:var(--orange);border-top-left-radius:26px;color:var(--white);font-family:'Oswald',sans-serif;font-weight:500;font-size:14.5px;line-height:31px;padding-left:23px;letter-spacing:.2px;border-top:3px solid var(--white);border-left:3px solid var(--white)}

.sec-head{display:flex;align-items:center;gap:8px;font-family:'Raleway',sans-serif;font-weight:700;font-size:14.5px;color:var(--navy);white-space:nowrap}
.dot{width:28px;height:28px;border-radius:50%;background:var(--orange);flex:none}
.dot.sm{width:30px;height:30px}

.col-right{left:257px;top:250px;width:257px;height:424px;background:var(--white);border-top-left-radius:24px}
.metrics{list-style:none;left:271px;top:343px;width:224px;font-size:7.8px;line-height:9.6px;font-weight:500}
.metrics li{position:relative;padding:2px 4px 2px 20px}
.metrics li:nth-child(odd){background:var(--row)}
.metrics li+li{margin-top:2px}
.tick{position:absolute;left:5px;top:3px;width:9px;height:9px}
.caps{list-style:none;font-size:9.4px;line-height:11.5px;color:var(--orange);font-weight:600}
.caps li{position:relative;padding-left:15px;margin-bottom:4px}
.caps .tick{left:0;top:1px;width:9px;height:9px}

/* footer */
.footer{left:0;top:671px;width:514px;height:55px;background:var(--navy)}
.footer::before{content:"";position:absolute;left:0;top:-5px;width:100%;height:6px;background:radial-gradient(circle at 5px 0,transparent 4px,var(--navy) 4.6px) repeat-x;background-size:10px 6px}
.info-tag{left:11px;top:664px;width:78px;height:44px;background:var(--orange);border-radius:12px;border:2px solid var(--orange-dark);color:var(--white);text-align:center;font-family:'Oswald',sans-serif;font-weight:600;line-height:8.6px;padding-top:8px}
.info-tag small{display:block;font-size:6.2px;font-weight:500}
.info-tag b{display:block;font-size:9.4px;font-weight:600}
.phone-ico{left:100px;top:681px;width:28px;height:32px}
.phone{left:135px;top:680px;font-family:'Montserrat',sans-serif;font-weight:800;font-size:19px;color:var(--white);letter-spacing:.3px}
.web{left:137px;top:703px;font-size:10.5px;color:var(--white);letter-spacing:1.3px;font-weight:600}
.vsep{top:683px;width:1.2px;height:29px;background:var(--orange)}
.pin{left:297px;top:689px;width:8px;height:11px}
.addr{left:307px;top:688px;font-size:9px;line-height:11.4px;color:var(--white)}
.social{top:692px;width:15px;height:15px;border-radius:50%;background:var(--orange)}

/* back */
.back-right{left:257px;top:0;width:257px;height:560px;background:var(--white);border-top-left-radius:30px}
.feature{left:20px;width:216px;border-top:1.4px solid var(--navy)}
.feature .sq,.value .sq{position:absolute;left:0;top:0;width:36px;height:39px}
.sq.navy{background:var(--navy)}
.sq.orange{background:var(--orange)}
.feature .txt{margin-left:43px;padding-top:4px}
.f-title{font-family:'Raleway',sans-serif;font-weight:800;font-size:10.6px;color:var(--navy);line-height:12px;margin-bottom:2px}
.f-title.orange{color:var(--orange)}
.f-body{font-size:7.6px;line-height:10.2px}
.value{left:276px;width:216px;border-top:1.4px solid var(--navy)}
.value .sq{width:34px}
.value .txt{margin-left:42px;padding-top:4px}
.values-band{left:300px;top:219px;width:214px;height:21px;background:var(--navy);color:var(--white);font-weight:600;font-size:14px;line-height:21px;padding-left:15px}
.values-dot{left:276px;top:212px;width:35px;height:35px;border-radius:50%;background:var(--orange);border:3px solid var(--white)}
.offices{left:0;top:550px;width:514px;height:124px;background:linear-gradient(180deg,#ee7a2a,#e97021);border-radius:26px 26px 0 0}
.offices-pill{left:172px;top:537px;width:172px;height:27px;background:var(--white);border:2px solid var(--orange);border-radius:14px;font-family:'Oswald',sans-serif;font-weight:500;font-size:15px;line-height:23px;text-align:center;color:var(--navy)}
.city{top:598px;width:78px;text-align:center;font-family:'Oswald',sans-serif;font-weight:500;font-size:10.5px;line-height:12.5px;color:var(--white)}
.city .map{display:block;margin:0 auto 8px;width:40px;height:26px;background:rgba(255,255,255,.18);border-radius:4px}
.city-sep{top:650px;width:1px;height:26px;background:rgba(255,255,255,.7)}
</style>
</head>
<body>

<!-- FRONT PAGE -->
<section class="page front">
  <div class="abs hero">
    <div class="hero-photo" role="img" aria-label="Photo of a young recruiting team talking together in a bright office"></div>
  </div>
  <div class="abs brand"><span class="brand-mark"></span><span class="brand-name">VELTRO GROUP</span></div>
  <h1 class="abs headline"><span class="hl">POWERING</span><br>PROGRESSION<br><span class="hl light">WITH </span><span class="hl">PEOPLE</span></h1>
  <p class="abs tagline">Recruitment solutions for an evolving marketplace</p>
  <div class="abs division-tab">DIVISION OVERVIEW – IT</div>

  <div class="abs col-right"></div>

  <div class="abs sec-head" style="left:18px;top:256px"><span class="dot"></span>Veltro <span class="hl" style="margin-left:-4px">Group</span></div>
  <div class="abs body-text" style="left:19px;top:291px;width:224px">
    <p>For over 20 years we have cultivated relationships with some of the most talented IT professionals. We are their trusted partner assisting them as they achieve their career goals. Our team is focused on matching that talent with the positions you have available and ensuring they align with your organization’s goals and culture. Finding the right talent takes time and you away from your work, let Veltro Group be your talent acquisition partner for your IT staffing needs.</p>
  </div>

  <div class="abs sec-head" style="left:18px;top:387px"><span class="dot"></span>Client <span class="hl" style="margin-left:-4px">Services</span></div>
  <div class="abs body-text" style="left:19px;top:422px;width:224px">
    <p>Our IT recruiting team understands the challenges facing hiring managers and the need to find the right people quickly. Our dynamic processes scale to meet the needs of ever-changing business environments. When you need IT resources for project or permanent opportunities, Veltro Group is committed to providing innovative solutions that deliver consistent results.</p>
  </div>

  <div class="abs sec-head" style="left:18px;top:500px"><span class="dot"></span>Strategic <span class="hl" style="margin-left:-4px">Staffing Model</span></div>
  <div class="abs body-text" style="left:19px;top:536px;width:224px">
    <p>Veltro Group partners with clients nationwide to deliver the right resources to meet project and permanent staffing goals. Your dedicated recruiting team is committed to matching you with top talent to meet budget and staffing goals, while maintaining consistency and communication throughout the recruiting process.</p>
    <p>We take the time to get to know you, your organization and culture to ensure we recruit the right professionals for your team. Then we take the same amount of care to get to know candidates so you only interview individuals with the right skillsets and career goals.</p>
  </div>

  <div class="abs body-text" style="left:273px;top:267px;width:223px">
    <p>Transparency and communication are at our core and you can expect to have one point of contact, fast feedback and open dialogue with our team throughout the recruiting process. As part of our commitment to transparency and process improvement, we monitor and provide metrics to ensure we always provide the best service to our clients, including</p>
  </div>

  <ul class="abs metrics">
    <li><svg class="tick" viewBox="0 0 10 10"><circle cx="5" cy="5" r="4.3" fill="none" stroke="#f07f2d" stroke-width="1"/><path d="M3 5.2l1.4 1.4L7.1 3.8" fill="none" stroke="#f07f2d" stroke-width="1"/></svg><span class="hl">Candidate Accuracy Rate:</span> percentage of presented candidates who interview</li>
    <li><svg class="tick" viewBox="0 0 10 10"><circle cx="5" cy="5" r="4.3" fill="none" stroke="#f07f2d" stroke-width="1"/><path d="M3 5.2l1.4 1.4L7.1 3.8" fill="none" stroke="#f07f2d" stroke-width="1"/></svg><span class="hl">Interview to Hire Rate:</span> percentage of interviewees who are hired</li>
    <li><svg class="tick" viewBox="0 0 10 10"><circle cx="5" cy="5" r="4.3" fill="none" stroke="#f07f2d" stroke-width="1"/><path d="M3 5.2l1.4 1.4L7.1 3.8" fill="none" stroke="#f07f2d" stroke-width="1"/></svg><span class="hl">Placement Success Rate:</span> customer satisfaction for each placement</li>
    <li><svg class="tick" viewBox="0 0 10 10"><circle cx="5" cy="5" r="4.3" fill="none" stroke="#f07f2d" stroke-width="1"/><path d="M3 5.2l1.4 1.4L7.1 3.8" fill="none" stroke="#f07f2d" stroke-width="1"/></svg><span class="hl">Fulfillment Ratio:</span> percentage of requests fulfilled vs. the competition</li>
    <li><svg class="tick" viewBox="0 0 10 10"><circle cx="5" cy="5" r="4.3" fill="none" stroke="#f07f2d" stroke-width="1"/><path d="M3 5.2l1.4 1.4L7.1 3.8" fill="none" stroke="#f07f2d" stroke-width="1"/></svg><span class="hl">Time to Fill Ratio:</span> time it takes from initial request to candidate presentation</li>
    <li><svg class="tick" viewBox="0 0 10 10"><circle cx="5" cy="5" r="4.3" fill="none" stroke="#f07f2d" stroke-width="1"/><path d="M3 5.2l1.4 1.4L7.1 3.8" fill="none" stroke="#f07f2d" stroke-width="1"/></svg><span class="hl">Total Billing:</span> total services billed per quarter</li>
  </ul>

  <div class="abs sec-head" style="left:269px;top:496px;align-items:center;line-height:15.5px"><span class="dot sm"></span><span>Enterprise Managed<br><span class="hl">Service Capabilities</span></span></div>
  <div class="abs body-text" style="left:273px;top:541px;width:223px;font-size:7.8px;line-height:10.3px">
    <p>Veltro Group works closely with enterprise clients who utilize VMS and MPS solutions and provide the following services as part of our commitment to our clients.</p>
  </div>
  <ul class="abs caps" style="left:273px;top:590px;width:100px">
    <li><svg class="tick" viewBox="0 0 10 10"><circle cx="5" cy="5" r="4.3" fill="none" stroke="#2c3a4c" stroke-width="1"/><path d="M3 5.2l1.4 1.4L7.1 3.8" fill="none" stroke="#2c3a4c" stroke-width="1"/></svg>Attract top talent</li>
    <li><svg class="tick" viewBox="0 0 10 10"><circle cx="5" cy="5" r="4.3" fill="none" stroke="#2c3a4c" stroke-width="1"/><path d="M3 5.2l1.4 1.4L7.1 3.8" fill="none" stroke="#2c3a4c" stroke-width="1"/></svg>Accountability</li>
    <li><svg class="tick" viewBox="0 0 10 10"><circle cx="5" cy="5" r="4.3" fill="none" stroke="#2c3a4c" stroke-width="1"/><path d="M3 5.2l1.4 1.4L7.1 3.8" fill="none" stroke="#2c3a4c" stroke-width="1"/></svg>Evaluation</li>
    <li><svg class="tick" viewBox="0 0 10 10"><circle cx="5" cy="5" r="4.3" fill="none" stroke="#2c3a4c" stroke-width="1"/><path d="M3 5.2l1.4 1.4L7.1 3.8" fill="none" stroke="#2c3a4c" stroke-width="1"/></svg>Customized<br>Reporting</li>
  </ul>
  <ul class="abs caps" style="left:382px;top:590px;width:110px">
    <li><svg class="tick" viewBox="0 0 10 10"><circle cx="5" cy="5" r="4.3" fill="none" stroke="#2c3a4c" stroke-width="1"/><path d="M3 5.2l1.4 1.4L7.1 3.8" fill="none" stroke="#2c3a4c" stroke-width="1"/></svg>Consolidated billing</li>
    <li><svg class="tick" viewBox="0 0 10 10"><circle cx="5" cy="5" r="4.3" fill="none" stroke="#2c3a4c" stroke-width="1"/><path d="M3 5.2l1.4 1.4L7.1 3.8" fill="none" stroke="#2c3a4c" stroke-width="1"/></svg>Standardized terms</li>
    <li><svg class="tick" viewBox="0 0 10 10"><circle cx="5" cy="5" r="4.3" fill="none" stroke="#2c3a4c" stroke-width="1"/><path d="M3 5.2l1.4 1.4L7.1 3.8" fill="none" stroke="#2c3a4c" stroke-width="1"/></svg>Structured approval process</li>
  </ul>

  <div class="abs footer"></div>
  <div class="abs info-tag"><small>We Are Here To Help</small><b>FOR MORE</b><b>INFORMATION</b></div>
  <svg class="abs phone-ico" viewBox="0 0 28 32"><rect x="6" y="1" width="16" height="30" rx="3" fill="#f07f2d"/><rect x="9" y="5" width="10" height="20" fill="#2c3a4c"/><circle cx="14" cy="28" r="1.3" fill="#2c3a4c"/></svg>
  <div class="abs phone">(615) 555-0142</div>
  <div class="abs web">www.veltrogroup.com</div>
  <div class="abs vsep" style="left:285px"></div>
  <svg class="abs pin" viewBox="0 0 8 11"><path d="M4 0.5a3.5 3.5 0 0 1 3.5 3.5C7.5 6.5 4 10.5 4 10.5S0.5 6.5 0.5 4A3.5 3.5 0 0 1 4 0.5z" fill="#f07f2d"/><circle cx="4" cy="4" r="1.3" fill="#2c3a4c"/></svg>
  <div class="abs addr">118 Harlow Ridge Drive Suite<br>400 Brentwood, TN 37027</div>
  <div class="abs vsep" style="left:437px"></div>
  <span class="abs social" style="left:450px"></span>
  <span class="abs social" style="left:468px"></span>
  <span class="abs social" style="left:486px"></span>
</section>

<!-- BACK PAGE -->
<section class="page back">
  <div class="abs back-right"></div>

  <div class="abs sec-head" style="left:18px;top:20px"><span class="dot"></span>Who is <span class="hl" style="margin-left:-4px">Veltro Group?</span></div>
  <div class="abs body-text" style="left:19px;top:62px;width:225px;font-size:7.9px;line-height:10.3px">
    <p>Veltro Group specializes in Accounting &amp; Finance, IT and Healthcare IT staffing. We put the right people in the right jobs for their career goals and the business goals of our clients.</p>
    <p>Our objective is to create long term relationships that exceed our client’s expectations. Our mission and values outline the commitments we make to each client and consultant.</p>
  </div>

  <div class="abs sec-head" style="left:18px;top:168px;line-height:15.5px"><span class="dot"></span><span>What makes<br><span class="hl">Veltro Group different?</span></span></div>
  <div class="abs body-text" style="left:19px;top:209px;width:225px;font-size:7.9px;line-height:10.3px;text-align:left">
    <p>There are many choices you can make for when looking for a staffing partner, and our goal is to be your staffing partner of choice.</p>
  </div>

  <div class="abs feature" style="top:255px"><span class="sq navy"></span><div class="txt"><div class="f-title orange">TEAM</div><div class="f-body">consists of passionate, experienced recruiters who place talent with our long-term partners.</div></div></div>
  <div class="abs feature" style="top:314px"><span class="sq orange"></span><div class="txt"><div class="f-title">STRATEGIC PARTNERSHIPS</div><div class="f-body">we work with clients whose values align with ours to provide world class recruiting services.</div></div></div>
  <div class="abs feature" style="top:373px"><span class="sq navy"></span><div class="txt"><div class="f-title orange">EXPERIENCE</div><div class="f-body">with 20 years in the industry, we know staffing and what makes a good team member for our clients. We have strong networks of professionals that includes some of the best in their respective industries</div></div></div>
  <div class="abs feature" style="top:459px"><span class="sq orange"></span><div class="txt"><div class="f-title">INTERNAL PROCESSES</div><div class="f-body">everything we do is driven by our internal processes to ensure the highest level of service and we review our metrics to ensure we work with the maximum efficiency.</div></div></div>

  <div class="abs brand" style="left:282px;top:14px"><span class="brand-mark" style="width:38px;height:38px"></span><span class="brand-name" style="color:var(--navy);font-size:19.5px;margin-top:11px">VELTRO GROUP</span></div>

  <div class="abs sec-head" style="left:276px;top:98px"><span class="dot sm"></span>Mission <span class="hl" style="margin-left:-4px">Statement</span></div>
  <div class="abs body-text" style="left:275px;top:139px;width:216px;font-size:7.9px;line-height:10.3px">
    <p>We consistently provide the highest level of value, service and respect to our customers. Our proven value is driven by professionals committed to providing a superior product. We will stop at nothing to provide the best level of service with organizations that recognize our value and look to establish long term relationships.</p>
  </div>

  <div class="abs values-band">Core Values</div>
  <span class="abs values-dot"></span>

  <div class="abs value" style="top:256px"><span class="sq navy"></span><div class="txt"><div class="f-title orange">INTEGRITY</div><div class="f-body">building trust through our honest and ethical business practices</div></div></div>
  <div class="abs value" style="top:307px"><span class="sq orange"></span><div class="txt"><div class="f-title">DEDICATION</div><div class="f-body">relentless pursuit of excellence through partnerships with our clients, consultants and internal employees</div></div></div>
  <div class="abs value" style="top:364px"><span class="sq navy"></span><div class="txt"><div class="f-title orange">RELIABILITY</div><div class="f-body">taking responsibility at a consistently high level of performance through our expertise and commitment</div></div></div>
  <div class="abs value" style="top:421px"><span class="sq orange"></span><div class="txt"><div class="f-title">VALUE</div><div class="f-body">through superior service driven actions, we provide unparalleled value to our clients and consultants</div></div></div>
  <div class="abs value" style="top:479px"><span class="sq navy"></span><div class="txt"><div class="f-title orange">UNITY</div><div class="f-body">developing a team environment that thrives on healthy competition and personal growth</div></div></div>

  <div class="abs offices" role="img" aria-label="Faded orange-tinted photo of an office team behind the location list"></div>
  <div class="abs offices-pill">OFFICE LOCATIONS</div>
  <div class="abs city" style="left:14px"><span class="map" role="img" aria-label="Outline map of Tennessee"></span>Headquarters in<br>NASHVILLE</div>
  <div class="abs city" style="left:95px"><span class="map" role="img" aria-label="Outline map of Georgia"></span>Atlanta, GA</div>
  <div class="abs city" style="left:176px"><span class="map" role="img" aria-label="Outline map of Alabama"></span>Birmingham, AL</div>
  <div class="abs city" style="left:267px"><span class="map" role="img" aria-label="Outline map of Florida"></span>Boca Raton, FL</div>
  <div class="abs city" style="left:345px"><span class="map" role="img" aria-label="Outline map of Colorado"></span>Denver, CO</div>
  <div class="abs city" style="left:415px"><span class="map" role="img" aria-label="Outline map of Kentucky"></span>Louisville, KY</div>
  <span class="abs city-sep" style="left:97px;top:640px"></span>
  <span class="abs city-sep" style="left:169px;top:640px"></span>
  <span class="abs city-sep" style="left:260px;top:640px"></span>
  <span class="abs city-sep" style="left:351px;top:640px"></span>
  <span class="abs city-sep" style="left:415px;top:640px"></span>

  <div class="abs footer"></div>
  <div class="abs info-tag"><small>We Are Here To Help</small><b>FOR MORE</b><b>INFORMATION</b></div>
  <svg class="abs phone-ico" viewBox="0 0 28 32"><rect x="6" y="1" width="16" height="30" rx="3" fill="#f07f2d"/><rect x="9" y="5" width="10" height="20" fill="#2c3a4c"/><circle cx="14" cy="28" r="1.3" fill="#2c3a4c"/></svg>
  <div class="abs phone">(615) 555-0142</div>
  <div class="abs web">www.veltrogroup.com</div>
  <div class="abs vsep" style="left:285px"></div>
  <svg class="abs pin" viewBox="0 0 8 11"><path d="M4 0.5a3.5 3.5 0 0 1 3.5 3.5C7.5 6.5 4 10.5 4 10.5S0.5 6.5 0.5 4A3.5 3.5 0 0 1 4 0.5z" fill="#f07f2d"/><circle cx="4" cy="4" r="1.3" fill="#2c3a4c"/></svg>
  <div class="abs addr">118 Harlow Ridge Drive Suite<br>400 Brentwood, TN 37027</div>
  <div class="abs vsep" style="left:437px"></div>
  <span class="abs social" style="left:450px"></span>
  <span class="abs social" style="left:468px"></span>
  <span class="abs social" style="left:486px"></span>
</section>

</body>
</html>
```